Automotive spring company needs banner for website

Banner dimensions: 3840 x 880 pixels
Banner need to be consistent with our branding (logo, stationary, colors, fonts, message).
People images should show happiness and it is preferable those people are in or around a car unless it ties into one of the 3 quotes in the must haves below.
Use color blue #4885ed
and gold color #f7d105
Minimal, strong, clean, & tech

35-55 male and female

Auto Repair

• Clickable element for "Shop" or "Make an Appointment"
• "25 Years of Customer Satisfaction" or
• "Get it Done Right by Specialist" or
• "Peace of Mind National Warranty"
• Use our font, Eurostile and/or complimentary font paring

```html
<!DOCTYPE html>
<html lang="en">
<head>
<meta charset="UTF-8">
<title>Helvarro — 25 Years of Customer Satisfaction</title>
<link href="https://fonts.googleapis.com/css2?family=Orbitron:wght@700;900&display=swap" rel="stylesheet">
<style>
  :root {
    --cream-light: #fbf6ec;
    --cream: #f4ead8;
    --ink: #262626;
    --brand-blue: #4885ed;
    --brand-blue-deep: #2f63d4;
    --brand-gold: #f7d105;
    --suit-navy: #1f2a3d;
    --suit-mid: #3a4a66;
    --skin: #c99a82;
    --white: #ffffff;
  }
  * { margin: 0; padding: 0; box-sizing: border-box; }
  html, body {
    width: 1200px;
    height: 275px;
    overflow: hidden;
    background: var(--cream-light);
  }
  .banner {
    position: relative;
    width: 1200px;
    height: 275px;
    overflow: hidden;
    background: linear-gradient(90deg, var(--cream) 0%, var(--cream-light) 60%, var(--cream) 100%);
    font-family: "Orbitron", "Arial Black", sans-serif;
    font-weight: 900;
    color: var(--ink);
  }
  .hero-photo {
    position: absolute;
    left: 0;
    top: 0;
    width: 540px;
    height: 270px;
    background:
      radial-gradient(ellipse 90px 110px at 170px 170px, var(--skin) 0%, rgba(201,154,130,0.6) 55%, transparent 100%),
      linear-gradient(100deg, var(--suit-navy) 0%, var(--suit-mid) 45%, rgba(58,74,102,0.4) 70%, transparent 100%);
    -webkit-mask-image: linear-gradient(90deg, #000 0%, #000 60%, transparent 100%);
            mask-image: linear-gradient(90deg, #000 0%, #000 60%, transparent 100%);
  }
  .headline {
    position: absolute;
    left: 698px;
    top: 42px;
    transform: translateX(-50%);
    text-align: center;
    text-transform: uppercase;
    white-space: nowrap;
    font-weight: 900;
  }
  .headline-number {
    display: block;
    font-size: 60px;
    line-height: 60px;
    letter-spacing: 2px;
    margin-bottom: 6px;
  }
  .headline-line {
    display: block;
    font-size: 27px;
    line-height: 37px;
    letter-spacing: 0.5px;
  }
  .brand-name {
    position: absolute;
    right: 66px;
    top: 20px;
    font-size: 26px;
    line-height: 30px;
    font-weight: 900;
    letter-spacing: 1px;
    color: var(--brand-gold);
    text-transform: uppercase;
  }
  .shop-button {
    position: absolute;
    left: 981px;
    top: 210px;
    width: 153px;
    height: 44px;
    display: flex;
    align-items: center;
    justify-content: center;
    border-radius: 4px;
    background: linear-gradient(180deg, var(--brand-blue) 0%, var(--brand-blue-deep) 100%);
    box-shadow: 0 2px 4px rgba(0,0,0,0.25);
    color: var(--white);
    font-size: 14px;
    font-weight: 900;
    letter-spacing: 0.5px;
    text-decoration: none;
    text-transform: uppercase;
  }
  .base-stripe {
    position: absolute;
    left: 0;
    bottom: 0;
    width: 100%;
    height: 5px;
    background: var(--brand-blue);
  }
</style>
</head>
<body>
  <div class="banner">
    <div class="hero-photo" role="img" aria-label="Smiling businessman in a navy suit and striped tie giving a thumbs up"></div>

    <h1 class="headline">
      <span class="headline-number">25</span>
      <span class="headline-line">Years of</span>
      <span class="headline-line">Customer</span>
      <span class="headline-line">Satisfaction</span>
    </h1>

    <div class="brand-name">Helvarro</div>

    <a class="shop-button" href="#">Shop Now</a>

    <div class="base-stripe"></div>
  </div>
</body>
</html>
```